QRV Advisors needs a web site

We need a web site for www.qrvadvisors-example.com. QRV is a mergers and acquisition consulting company that focuses our buyer and seller services on logistics companies. We help put companies together, and help with legal and financial due diligence. We want the web site to express our service and show the logistics components. We want personalized images versus pictures of trucks and airplanes.

Our new logo uses Burgandy and grey colors. Image attached. We are not in to bold, big letters...classy, artistic, low key preferred. Confidentiality, experience, professional are what we want to express on the site.

All we expect for the first part of this project is a home page, and one subpage.  We are budgeting other funds for the technical aspects of the web site

Reason: All that I'm seeing so far is trucks, forklifts and planes. We are a legal mergers and acquisitions firm that focus on logistics. I like some of the images to say logistics, but really want it say legal, financial, and putting companies together. Will pay extra for the sub page if someone can impress us with a home page.

Reason: Swamped with another project at the moment...will work on this over the weekend and provide designer feedback and select final design by Tuesday

```html
<!DOCTYPE html>
<html lang="en">
<head>
<meta charset="utf-8">
<title>QRV Advisors</title>
<link href="https://fonts.googleapis.com/css2?family=Ubuntu:wght@400;500&family=Lato:wght@400;700&display=swap" rel="stylesheet">
<style>
:root{
  --burgundy:#a3002f;
  --burgundy-dark:#8a0028;
  --charcoal:#333333;
  --grey:#555555;
  --grey-mid:#888888;
  --panel:#f5f4f4;
  --line:#dddddd;
  --white:#ffffff;
}
*{box-sizing:border-box;margin:0;padding:0}
html,body{width:1174px;height:1200px;overflow:hidden;background:var(--white)}
body{font-family:'Lato',sans-serif;color:var(--grey);position:relative}
.page{position:relative;width:1174px;height:1200px;overflow:hidden}

.site-header{position:absolute;left:0;top:0;width:100%;height:103px;background:linear-gradient(#ffffff,#e9e9e9)}
.brand{position:absolute;left:121px;top:28px;display:flex;align-items:center;gap:12px;font-family:'Ubuntu',sans-serif;font-weight:400;font-size:40px;color:var(--burgundy);letter-spacing:1px}
.brand-mark{width:22px;height:22px;background:var(--burgundy)}
.phone{position:absolute;right:128px;top:38px;display:flex;align-items:center;gap:14px;font-family:'Ubuntu',sans-serif;font-size:23px;color:var(--burgundy)}

.main-nav{position:absolute;left:0;top:103px;width:100%;height:50px;background:#3b3b3b;border-top:1px solid #222}
.main-nav ul{list-style:none;display:flex;position:absolute;left:123px;top:0;height:50px}
.main-nav li{font-family:'Ubuntu',sans-serif;font-size:17.5px;color:var(--white);padding:0 8px;line-height:50px;border-right:1px solid #222;white-space:nowrap}
.main-nav li.active{background:linear-gradient(#fff,#e4e4e4);color:var(--burgundy);width:90px;text-align:center;border:none}
.main-nav li:nth-child(2){padding-left:14px}
.search{position:absolute;left:827px;top:9px;width:214px;height:28px;background:#8e8e8e;color:#e6e6e6;font-size:13px;padding:6px 10px;border-radius:2px}
.search svg{position:absolute;right:8px;top:6px}

.hero{position:absolute;left:0;top:153px;width:100%;height:336px;background:linear-gradient(100deg,#e8e3de 0%,#c8b7a8 25%,#2f3b55 45%,#d9c7b6 65%,#f1ece6 80%,#3c4a66 100%)}
.hero-caption{position:absolute;left:0;bottom:0;width:100%;height:47px;background:rgba(30,30,30,.82);color:var(--white);font-size:21px;line-height:44px;padding-left:131px;white-space:nowrap}
.dots{position:absolute;right:128px;top:17px;display:flex;gap:9px}
.dots span{width:10px;height:10px;border-radius:50%;background:#e6e6e6}
.dots span.on{background:var(--burgundy)}

.services{position:absolute;left:304px;top:482px;width:564px;height:84px;background:linear-gradient(#f6f6f6,#e4e4e4);border-radius:6px;box-shadow:0 3px 5px rgba(0,0,0,.25)}
.services svg{position:absolute}
.service-label{position:absolute;top:23px;font-family:'Ubuntu',sans-serif;font-size:17px;color:var(--burgundy);line-height:20px;letter-spacing:.3px;white-space:nowrap}
.divider{position:absolute;top:12px;width:1px;height:60px;background:#cfcfcf}

.panel{position:absolute;top:615px;width:296px;height:299px;background:var(--panel);border:1px solid var(--line)}
.panel-title{position:absolute;left:50%;top:-6px;transform:translateX(-50%);width:187px;height:31px;background:var(--burgundy);color:var(--white);font-family:'Ubuntu',sans-serif;font-weight:500;font-size:17px;text-align:center;line-height:31px;border-radius:0 0 4px 4px}
.btn{position:absolute;right:14px;bottom:-1px;background:var(--charcoal);color:var(--white);font-size:13px;padding:2px 9px;border-radius:4px 4px 0 0}
.mission-photo{position:absolute;left:12px;top:47px;width:272px;height:94px;border:3px solid #fff;outline:1px solid #ddd;background:linear-gradient(90deg,#6a5848,#d7c3a8,#8b7a6a,#d9cbb6,#5b5146)}
.mission-text{position:absolute;left:16px;top:155px;width:266px;font-size:12.5px;line-height:18.3px;color:#555}
.news-item{position:absolute;left:14px;width:270px;display:flex;gap:14px;padding-bottom:12px}
.news-item+.news-item{border-top:1px solid #d6d6d6}
.date{width:34px;flex:none;text-align:center}
.date .m{background:var(--charcoal);color:#fff;font-size:12px;line-height:16px;border-radius:3px 3px 0 0}
.date .d{background:#dcdcdc;color:#444;font-size:17px;line-height:25px}
.news-item h4{font-weight:400;font-size:13.5px;color:#333;margin-bottom:2px}
.news-item p{font-size:12px;line-height:17px;color:#555}
.form-row{position:absolute;left:19px;font-size:13.5px;color:#555}
.field{position:absolute;left:91px;width:187px;height:22px;background:#fff;border:1px solid #cfcfcf}

.partners{position:absolute;left:0;top:946px;width:100%;height:66px}
.partner{position:absolute;top:18px;font-family:'Ubuntu',sans-serif;font-weight:500;font-size:22px;color:#2a5fa8;white-space:nowrap}
.partner small{display:block;font-family:'Lato',sans-serif;font-weight:400;font-size:9px;color:#333}

.site-footer{position:absolute;left:0;top:1032px;width:100%;height:168px;background:var(--burgundy);color:var(--white);border-top:3px solid var(--burgundy-dark)}
.footer-col{position:absolute;top:15px}
.footer-col h3{font-family:'Ubuntu',sans-serif;font-weight:400;font-size:18px;margin-bottom:10px}
.footer-col ul{list-style:none;font-size:13.5px;line-height:19.6px}
.footer-col p{font-size:12.5px;line-height:16px}
.email-box{width:200px;height:23px;background:#fff;color:#999;font-size:12.5px;padding:3px 9px;margin-top:13px;border-radius:2px}
.subscribe{display:inline-block;margin-top:14px;background:#333;padding:2px 7px;font-size:14px;border-radius:2px}
.social li{display:flex;align-items:center;gap:10px;margin-bottom:12px}
.social i{width:25px;height:25px;background:var(--white);opacity:.9;border-radius:3px}
.footer-brand{position:absolute;left:805px;top:20px;width:260px;text-align:center}
.footer-brand b{display:block;font-family:'Ubuntu',sans-serif;font-weight:500;font-size:54px;letter-spacing:4px;line-height:62px;margin-bottom:10px}
.footer-brand span{font-size:13px;line-height:19px}
</style>
</head>
<body>
<div class="page">
  <header class="site-header">
    <div class="brand"><span class="brand-mark"></span>QRV Advisors</div>
    <div class="phone">
      <svg width="26" height="26" viewBox="0 0 26 26"><circle cx="13" cy="13" r="11.5" fill="none" stroke="#777" stroke-width="1.5"/><path d="M9 7c1-1 2 0 3 2s-1 2 0 3 2 3 3 3 1-2 3-1 1 3 0 3c-3 2-11-6-9-10z" fill="#777"/></svg>
      123 456 7890
    </div>
  </header>

  <nav class="main-nav">
    <ul>
      <li class="active">Home</li>
      <li>About Us</li>
      <li>Consulting Services</li>
      <li>News &amp; Events</li>
      <li>FAQ's</li>
      <li>Contact Us</li>
    </ul>
    <div class="search">Search
      <svg width="15" height="15" viewBox="0 0 15 15"><circle cx="6" cy="6" r="4.5" fill="none" stroke="#fff" stroke-width="2"/><path d="M9.5 9.5l4 4" stroke="#fff" stroke-width="2.4"/></svg>
    </div>
  </nav>

  <section class="hero" role="img" aria-label="Photo of smiling business advisors in conversation at a meeting">
    <div class="hero-caption">QRV Services Are Offered By Industry Executives With Extensive M&amp;A Experience
      <div class="dots"><span class="on"></span><span></span><span></span><span></span><span></span></div>
    </div>
  </section>

  <div class="services">
    <svg style="left:10px;top:12px" width="58" height="62" viewBox="0 0 62 64"><rect x="4" y="4" width="42" height="54" rx="3" fill="none" stroke="#555" stroke-width="3"/><rect x="10" y="10" width="42" height="50" rx="3" fill="#f2f2f2" stroke="#555" stroke-width="3"/><path d="M17 22h26M17 30h26M17 38h18M17 46h14" stroke="#555" stroke-width="3"/><path d="M36 48l6 6 14-16" fill="none" stroke="#555" stroke-width="4"/></svg>
    <span class="service-label" style="left:73px">Bussiness<br>&amp; Planning</span>
    <span class="divider" style="left:176px"></span>
    <svg style="left:196px;top:9px" width="48" height="68" viewBox="0 0 50 70"><path d="M25 0L10 30h8v14L4 70h14l7-14 7 14h14L32 44V30h8z" fill="#555"/></svg>
    <span class="service-label" style="left:254px">Mergers<br>&amp; Acquisition</span>
    <span class="divider" style="left:376px"></span>
    <svg style="left:393px;top:9px" width="66" height="66" viewBox="0 0 70 70"><circle cx="35" cy="35" r="32" fill="none" stroke="#555" stroke-width="5"/><circle cx="35" cy="35" r="25" fill="#f0f0f0" stroke="#555" stroke-width="2"/><path d="M26 22l16 20-4 8-8-4-16-20z" fill="none" stroke="#555" stroke-width="3"/></svg>
    <span class="service-label" style="left:480px">Advisory<br>Services</span>
  </div>

  <section class="panel" style="left:121px">
    <div class="panel-title">Our Mission</div>
    <div class="mission-photo" role="img" aria-label="Group photo of a diverse professional team"></div>
    <p class="mission-text">Lorem Ipsum is simply dummy text of the printing and typesetting industry. Lorem Ipsum has been the industry's standard dummy text ever since the 1500sstandard dummy text ever since the 1500s dustry. Lorem Idustry. Lorem I dustry. Lorem.,</p>
    <span class="btn">Read More</span>
  </section>

  <section class="panel" style="left:440px">
    <div class="panel-title">News &amp; Events</div>
    <div class="news-item" style="top:42px">
      <div class="date"><div class="m">APR</div><div class="d">02</div></div>
      <div><h4>Lorem ipsum dolor sit amet</h4><p>Lorem ipsum dol adipiscing elit, seder or sit amet, consectetu industry's standard dummy text ever er</p></div>
    </div>
    <div class="news-item" style="top:119px;padding-top:9px">
      <div class="date"><div class="m">APR</div><div class="d">02</div></div>
      <div><h4>Lorem ipsum dolor sit amet</h4><p>Lorem ipsum dol adipiscing elit, seder or sit amet, consectetu industry's standard dummy text ever er</p></div>
    </div>
    <div class="news-item" style="top:208px;padding-top:11px">
      <div class="date"><div class="m">APR</div><div class="d">02</div></div>
      <div><h4>Lorem ipsum dolor sit amet</h4><p>Lorem ipsum dol adipiscing elit, seder or sit amet, consectetu</p></div>
    </div>
    <span class="btn">Read More</span>
  </section>

  <section class="panel" style="left:758px">
    <div class="panel-title">Get in touch</div>
    <div class="form-row" style="top:50px">Name</div><div class="field" style="top:44px"></div>
    <div class="form-row" style="top:95px">Phone</div><div class="field" style="top:89px"></div>
    <div class="form-row" style="top:139px">Email</div><div class="field" style="top:133px"></div>
    <div class="form-row" style="top:183px">Message</div><div class="field" style="top:177px;height:68px"></div>
    <span class="btn" style="padding:2px 15px">Submit</span>
  </section>

  <section class="partners">
    <svg style="position:absolute;left:137px;top:22px" width="18" height="30" viewBox="0 0 18 30"><path d="M15 2L3 15l12 13" fill="none" stroke="#999" stroke-width="4"/></svg>
    <div class="partner" style="left:240px">Halvorne</div>
    <div class="partner" style="left:428px;top:12px;color:#1f3a6e">Cardessa Logistics<small>Member of Orvale Group</small></div>
    <div class="partner" style="left:626px;color:#1f3a8a">Tollvane Fleet</div>
    <div class="partner" style="left:845px;color:#666">Ridemoor</div>
    <svg style="position:absolute;left:1031px;top:22px" width="18" height="30" viewBox="0 0 18 30"><path d="M3 2l12 13L3 28" fill="none" stroke="#999" stroke-width="4"/></svg>
  </section>

  <footer class="site-footer">
    <div class="footer-col" style="left:137px">
      <h3>Quick Links</h3>
      <ul><li>Home</li><li>About Us</li><li>Consulting Services</li><li>News &amp; Events</li><li>FAQ's</li><li>Contact Us</li></ul>
    </div>
    <div class="footer-col" style="left:337px">
      <h3>Newsletter</h3>
      <p>Lorem Ipsum is simply dummy text of the<br>printing and typesetting industry.</p>
      <div class="email-box">your e-mail address</div>
      <span class="subscribe">Subscribe</span>
    </div>
    <div class="footer-col" style="left:635px">
      <h3>Follow Us</h3>
      <ul class="social"><li><i></i>Friendbook</li><li><i></i>Chirper</li><li><i></i>Linkpro</li></ul>
    </div>
    <div class="footer-brand">
      <b>QRV</b>
      <span>© 2014 QRVadvisors.<br>All Rights Reserved</span>
    </div>
  </footer>
</div>
</body>
</html>
```